Landscape design build company door flyer

I would like this flyer to convey a high-level of professionalism for a company that is excellent with communication with their clients as well as a company that does incredible installations

Went on vacation/holiday

```html
<!DOCTYPE html>
<html lang="en">
<head>
<meta charset="utf-8">
<title>Summit Stone Builders – Outdoor Living Spaces Flyer</title>
<link href="https://fonts.googleapis.com/css2?family=Barlow+Semi+Condensed:wght@700;800&family=Poppins:wght@400;500;600;800&display=swap" rel="stylesheet">
<style>
  :root {
    --navy: #0c2b3f;
    --orange: #f26f0c;
    --gold: #f2a724;
    --paper: #f1f1f1;
    --ink: #1b1b1b;
    --backdrop: #e6e6e6;
  }
  * { margin: 0; padding: 0; box-sizing: border-box; }
  html, body { width: 1200px; height: 1029px; overflow: hidden; background: var(--backdrop); }
  .flyer {
    position: absolute; left: 205px; top: 0;
    width: 790px; height: 1029px;
    background: var(--paper);
    overflow: hidden;
    font-family: "Poppins", sans-serif;
    color: var(--ink);
  }
  .hero-art { position: absolute; left: 0; top: 0; width: 790px; height: 484px; }
  .brand { position: absolute; left: 52px; top: 62px; width: 190px; text-align: center; }
  .brand-mark { width: 14px; height: 14px; border-radius: 50%; background: var(--orange); margin: 0 auto 10px; }
  .brand-name { font-family: "Poppins", sans-serif; font-weight: 600; font-size: 17px; color: var(--orange); letter-spacing: 0.3px; line-height: 1; }
  .brand-tag { font-size: 8px; font-weight: 500; color: var(--navy); letter-spacing: 0.3px; margin-top: 3px; }
  .headline {
    position: absolute; left: 26px; top: 206px;
    font-family: "Barlow Semi Condensed", sans-serif; font-weight: 800;
    font-size: 58px; line-height: 58px; color: #fff; letter-spacing: 0.2px;
  }
  .headline .accent { color: var(--orange); display: block; }
  .headline .line { display: block; }
  .section-title { font-weight: 800; font-size: 23px; color: var(--navy); line-height: 1; letter-spacing: -0.3px; }
  .section-title::after { content: ""; display: block; width: 68px; height: 3px; border-radius: 2px; background: var(--gold); margin-top: 6px; }
  .about { position: absolute; left: 26px; top: 503px; width: 338px; }
  .about p { margin-top: 13px; font-size: 12.4px; line-height: 15.2px; text-align: justify; hyphens: auto; }
  .services { position: absolute; left: 429px; top: 503px; }
  .service-list { list-style: none; margin-top: 10px; }
  .service-list li { display: flex; align-items: center; height: 21.6px; font-size: 14px; font-weight: 500; }
  .service-list svg { width: 12px; height: 12px; margin-right: 16px; flex: none; }
  .works-rule { position: absolute; left: 16px; top: 739.5px; width: 745px; height: 1.5px; background: var(--gold); }
  .works-title {
    position: absolute; left: 272px; top: 721px; width: 226px; height: 30px;
    background: var(--orange); color: #fff; text-align: center;
    font-weight: 800; font-size: 19px; line-height: 30px; letter-spacing: -0.2px;
  }
  .work { position: absolute; top: 766px; height: 118px; }
  .work-1 { left: 26px; width: 216px; background: linear-gradient(160deg, #6a625a 0%, #b48b78 45%, #c9a494 75%, #8c7a6c 100%); }
  .work-2 { left: 281px; width: 216px; background: linear-gradient(170deg, #4d5a4a 0%, #6f7579 30%, #a9adb0 65%, #7c8083 100%); }
  .work-3 { left: 533px; width: 210px; background: linear-gradient(160deg, #5b6550 0%, #4f6b3d 40%, #8d8e92 75%, #a6a8aa 100%); }
  .footer-art { position: absolute; left: 0; top: 927px; width: 790px; height: 102px; }
  .phone { position: absolute; left: 26px; top: 953px; display: flex; align-items: center; }
  .phone-icon { width: 53px; height: 51px; background: var(--orange); display: flex; align-items: center; justify-content: center; }
  .phone-number { margin-left: 13px; font-family: "Barlow Semi Condensed", sans-serif; font-weight: 800; font-size: 56px; line-height: 1; color: #fff; letter-spacing: -0.5px; }
  .contact { position: absolute; left: 514px; top: 947px; list-style: none; color: #fff; font-size: 14.5px; }
  .contact li { display: flex; align-items: center; height: 26px; }
  .contact svg { width: 18px; height: 14px; margin-right: 18px; flex: none; }
</style>
</head>
<body>
<main class="flyer">
  <svg class="hero-art" viewBox="0 0 790 484" aria-hidden="false">
    <defs>
      <linearGradient id="heroPhoto" x1="0" y1="0" x2="0.4" y2="1">
        <stop offset="0" stop-color="#c9c9c7"/>
        <stop offset="0.3" stop-color="#b98d68"/>
        <stop offset="0.6" stop-color="#8f9290"/>
        <stop offset="0.82" stop-color="#5b8d2f"/>
        <stop offset="1" stop-color="#3f7a1f"/>
      </linearGradient>
    </defs>
    <polygon points="355,0 790,0 790,484 300,484" fill="url(#heroPhoto)" role="img" aria-label="Photo of a two-level cedar deck with railings and stairs over a green lawn"/>
    <polygon points="0,163 358,163 522,484 0,484" fill="var(--navy)"/>
  </svg>

  <div class="brand">
    <div class="brand-mark"></div>
    <div class="brand-name">SUMMIT STONE BUILDERS</div>
    <div class="brand-tag">OUTDOOR LIVING SPACES</div>
  </div>

  <h1 class="headline">
    <span class="line">LET’S CREATE</span>
    <span class="line">YOUR DREAM</span>
    <span class="accent">OUTDOOR</span>
    <span class="accent">LIVING SPACE!</span>
  </h1>

  <section class="about">
    <h2 class="section-title">ABOUT US</h2>
    <p>Discover the endless possibilities for your outdoor space with The Summit Stone Builders Team. Our team of skilled artisans is dedicated to turning your outdoor space into a breathtaking oasis that you’ll love coming home to. Whether it’s a cozy patio for intimate gatherings, a sprawling deck to host memorable parties, or a custom paver driveway that adds instant curb appeal, our high-quality craftsmanship ensures stunning results that exceed your expectations.</p>
  </section>

  <section class="services">
    <h2 class="section-title">OUR SERVICES</h2>
    <ul class="service-list">
      <li><svg viewBox="0 0 12 12"><circle cx="6" cy="6" r="6" fill="var(--orange)"/><path d="M3.2 6.2l1.9 1.9 3.7-3.9" stroke="#fff" stroke-width="1.5" fill="none"/></svg>Paver Patios</li>
      <li><svg viewBox="0 0 12 12"><circle cx="6" cy="6" r="6" fill="var(--orange)"/><path d="M3.2 6.2l1.9 1.9 3.7-3.9" stroke="#fff" stroke-width="1.5" fill="none"/></svg>Paver Driveways</li>
      <li><svg viewBox="0 0 12 12"><circle cx="6" cy="6" r="6" fill="var(--orange)"/><path d="M3.2 6.2l1.9 1.9 3.7-3.9" stroke="#fff" stroke-width="1.5" fill="none"/></svg>Retaining Walls</li>
      <li><svg viewBox="0 0 12 12"><circle cx="6" cy="6" r="6" fill="var(--orange)"/><path d="M3.2 6.2l1.9 1.9 3.7-3.9" stroke="#fff" stroke-width="1.5" fill="none"/></svg>Decks &amp; Railings</li>
      <li><svg viewBox="0 0 12 12"><circle cx="6" cy="6" r="6" fill="var(--orange)"/><path d="M3.2 6.2l1.9 1.9 3.7-3.9" stroke="#fff" stroke-width="1.5" fill="none"/></svg>Pools</li>
      <li><svg viewBox="0 0 12 12"><circle cx="6" cy="6" r="6" fill="var(--orange)"/><path d="M3.2 6.2l1.9 1.9 3.7-3.9" stroke="#fff" stroke-width="1.5" fill="none"/></svg>Outdoor Lighting</li>
      <li><svg viewBox="0 0 12 12"><circle cx="6" cy="6" r="6" fill="var(--orange)"/><path d="M3.2 6.2l1.9 1.9 3.7-3.9" stroke="#fff" stroke-width="1.5" fill="none"/></svg>Firepits &amp; Fireplaces</li>
    </ul>
  </section>

  <div class="works-rule"></div>
  <h2 class="works-title">OUR WORKS</h2>
  <div class="work work-1" role="img" aria-label="Photo of composite deck steps beside a covered hot tub"></div>
  <div class="work work-2" role="img" aria-label="Photo of a grey composite deck with black metal railing"></div>
  <div class="work work-3" role="img" aria-label="Photo of a landscaped garden slope with stone steps and paver patio"></div>

  <svg class="footer-art" viewBox="0 0 790 102" aria-hidden="true">
    <rect x="0" y="7" width="790" height="95" fill="var(--navy)"/>
    <polygon points="477,0 790,0 790,102 433,102" fill="var(--orange)"/>
  </svg>

  <div class="phone">
    <div class="phone-icon">
      <svg width="28" height="28" viewBox="0 0 24 24"><path d="M6.6 2.5c.6-.3 1.3-.1 1.6.5l2 3.6c.3.6.2 1.3-.3 1.7l-1.5 1.2c.9 2 2.4 3.6 4.3 4.7l1.3-1.4c.4-.5 1.1-.6 1.7-.3l3.6 1.9c.6.3.8 1 .6 1.6l-.9 2.4c-.3.9-1.2 1.4-2.1 1.3C9.8 18.8 4.3 13 3.6 6c-.1-.9.4-1.8 1.3-2.1z" fill="#fff"/></svg>
    </div>
    <span class="phone-number">206-555-0148</span>
  </div>

  <ul class="contact">
    <li><svg viewBox="0 0 18 14"><rect x="0" y="0" width="18" height="14" rx="1.5" fill="#fff"/><path d="M1 1.5l8 6 8-6" stroke="var(--orange)" stroke-width="1.6" fill="none"/></svg>info@summitstonebuilders.com</li>
    <li><svg viewBox="0 0 18 14"><g fill="none" stroke="#fff" stroke-width="1.1"><circle cx="9" cy="7" r="6.3"/><ellipse cx="9" cy="7" rx="2.7" ry="6.3"/><path d="M2.7 7h12.6M3.6 4h10.8M3.6 10h10.8"/></g></svg>www.summitstonebuilders.com</li>
  </ul>
</main>
</body>
</html>
```